BRIGHT RIVER POWER.

I'd like my business logo.
contact name: Dennis Halvorsen
phone:0438759164
email: info@brightriverpower.net.au
website: www.brightriverpower.net.au

services:
solar
battery storage
LED lighting
energy saving solutions
general electrical
I'd like the design to look professional

Target Market(s)

Everyone

Industry/Entity Type

Business

Contact Information for Business Card

as described above

Requirements
Must have
• Id like the colours and the design to work well with my logo.

```html
<!DOCTYPE html>
<html lang="en">
<head>
<meta charset="utf-8">
<title>Bright River Power – Business Card</title>
<link rel="stylesheet" href="https://fonts.googleapis.com/css2?family=Source+Sans+3:wght@400;600&display=swap">
<style>
  :root {
    --backdrop: #161616;
    --card: #ffffff;
    --green: #5fb52d;
    --green-dark: #4aa52a;
    --orange: #f6a01a;
  }
  * { margin: 0; padding: 0; box-sizing: border-box; }
  html, body {
    width: 1200px;
    height: 900px;
    overflow: hidden;
    background: var(--backdrop);
    font-family: "Source Sans 3", "Myriad Pro", Arial, sans-serif;
  }
  .stage { position: relative; width: 1200px; height: 900px; }
  .card {
    position: absolute;
    top: 306px;
    height: 271px;
    background: var(--card);
    border-radius: 10px;
  }
  .card--front { left: 149px; width: 439px; }
  .card--back { left: 608px; width: 441px; }

  .mark-dot {
    position: absolute;
    left: 212px; top: 388px;
    width: 104px; height: 104px;
    border-radius: 50%;
    background: var(--orange);
  }
  .contact-name {
    position: absolute;
    left: 357px; top: 398px;
    font-size: 15px; font-weight: 600;
    color: var(--orange);
    white-space: nowrap;
  }
  .contact-list {
    position: absolute;
    left: 357px; top: 446px;
    list-style: none;
  }
  .contact-list li {
    display: flex; align-items: center;
    height: 16px;
    font-size: 12.5px;
    color: var(--green);
  }
  .contact-list svg { width: 9px; height: 9px; margin-right: 7px; fill: var(--orange); flex: none; }

  .brand {
    position: absolute;
    left: 608px; top: 395px;
    width: 441px;
    display: flex; align-items: center; justify-content: center;
    gap: 10px;
  }
  .brand-dot { width: 22px; height: 22px; border-radius: 50%; background: var(--orange); }
  .brand-name {
    font-size: 26px; font-weight: 600;
    color: var(--green);
    letter-spacing: 0.5px;
  }
  .services-title {
    position: absolute;
    left: 608px; top: 480px; width: 441px;
    text-align: center;
    font-size: 14px; font-weight: 600;
    color: var(--green-dark);
  }
  .services {
    position: absolute;
    left: 608px; top: 509px; width: 441px;
    text-align: center;
    font-size: 12.5px; line-height: 16px;
    color: var(--orange);
  }
</style>
</head>
<body>
<main class="stage">
  <section class="card card--front" aria-label="Card front"></section>
  <div class="mark-dot" aria-hidden="true"></div>
  <p class="contact-name">Dennis Halvorsen</p>
  <ul class="contact-list">
    <li><svg viewBox="0 0 10 10"><path d="M2 0.5 L3.6 0.5 L4.2 2.8 L3.1 3.6 C3.7 5 5 6.3 6.4 6.9 L7.2 5.8 L9.5 6.4 L9.5 8 C9.5 9 8.7 9.5 8 9.5 C4 9.2 0.8 6 0.5 2 C0.5 1.3 1 0.5 2 0.5 Z"/></svg>0438759164</li>
    <li><svg viewBox="0 0 10 10"><path d="M0.5 2 H9.5 V8.5 H0.5 Z" /><path d="M0.5 2 L5 5.5 L9.5 2" fill="none" stroke="#fff" stroke-width="1"/></svg>info@brightriverpower.net.au</li>
    <li><svg viewBox="0 0 10 10"><circle cx="5" cy="5" r="4.6"/><path d="M0.6 5 H9.4 M5 0.5 C2.8 3 2.8 7 5 9.5 M5 0.5 C7.2 3 7.2 7 5 9.5" fill="none" stroke="#fff" stroke-width="0.8"/></svg>www.brightriverpower.net.au</li>
  </ul>

  <section class="card card--back" aria-label="Card back"></section>
  <div class="brand">
    <span class="brand-dot" aria-hidden="true"></span>
    <span class="brand-name">BRIGHT RIVER POWER</span>
  </div>
  <h2 class="services-title">WHAT I DO</h2>
  <p class="services">Solar | Battery Storage<br>LED Lighting | Energy Saving Solutions</p>
</main>
</body>
</html>
```